Harbor Loom Floors Letterhead

Letterhead used for business reasons. It must be editable and easy to use.

Address is 2715 W. Pelican Lane Cedar Cove ST 34187 - 555.382.6519

```html
<!DOCTYPE html>
<html lang="en">
<head>
<meta charset="utf-8">
<title>Harbor Loom Floors Letterhead</title>
<link rel="stylesheet" href="https://fonts.googleapis.com/css2?family=Lato:wght@400;700&family=Montserrat:wght@400;500&family=Tangerine:wght@700&display=swap">
<style>
  :root {
    --backdrop: #e3e3e3;
    --paper: #ffffff;
    --band: #161616;
    --accent: #e0912a;
    --band-text: #f2f2f2;
    --ink: #141414;
  }
  * { margin: 0; padding: 0; box-sizing: border-box; }
  html, body {
    width: 1200px;
    height: 1079px;
    overflow: hidden;
    background: var(--backdrop);
  }
  .letterhead {
    position: absolute;
    left: 225px;
    top: 10px;
    width: 750px;
    height: 1060px;
    background: var(--paper);
    color: var(--ink);
    font-family: "Lato", sans-serif;
  }
  .masthead {
    position: absolute;
    left: 0; top: 0;
    width: 100%;
    height: 171px;
    background: var(--band);
  }
  .brand-name {
    position: absolute;
    left: 37px;
    top: 42px;
    font-family: "Montserrat", sans-serif;
    font-weight: 500;
    font-size: 34px;
    line-height: 42px;
    color: var(--accent);
  }
  .masthead-divider {
    position: absolute;
    left: 533px;
    top: 60px;
    width: 2px;
    height: 55px;
    background: var(--accent);
  }
  .contact {
    position: absolute;
    left: 567px;
    top: 57px;
    font-family: "Montserrat", sans-serif;
    font-size: 13.5px;
    line-height: 18px;
    color: var(--band-text);
    font-style: normal;
  }
  .contact-phone {
    display: flex;
    align-items: center;
    gap: 6px;
    margin-top: 9px;
    margin-left: -2px;
  }
  .contact-phone svg { width: 11px; height: 11px; }
  .letter-body {
    position: absolute;
    left: 37px;
    right: 37px;
    top: 0;
    font-size: 15px;
    line-height: 17.5px;
  }
  .letter-date { position: absolute; top: 243px; }
  .recipient { position: absolute; top: 280px; }
  .recipient-company { position: absolute; top: 357px; }
  .salutation {
    position: absolute;
    top: 455px;
    font-size: 18.5px;
    font-weight: 700;
  }
  .letter-text {
    position: absolute;
    top: 521px;
    left: 0; right: 0;
  }
  .letter-text p {
    text-align: justify;
    line-height: 16.5px;
    margin-bottom: 16.5px;
  }
  .closing { position: absolute; top: 823px; }
  .signature {
    position: absolute;
    top: 900px;
    font-family: "Tangerine", cursive;
    font-weight: 700;
    font-size: 44px;
    line-height: 50px;
  }
</style>
</head>
<body>
  <article class="letterhead">
    <header class="masthead">
      <div class="brand-name">Harbor Loom<br>Floors</div>
      <div class="masthead-divider"></div>
      <address class="contact">
        <div>2715 W. Pelican Lane</div>
        <div>Cedar Cove ST 34187</div>
        <div class="contact-phone">
          <svg viewBox="0 0 24 24" aria-hidden="true"><path fill="var(--accent)" d="M6.6 10.8a15.1 15.1 0 0 0 6.6 6.6l2.2-2.2a1 1 0 0 1 1-.25 11.4 11.4 0 0 0 3.6.57 1 1 0 0 1 1 1V20a1 1 0 0 1-1 1A17 17 0 0 1 3 4a1 1 0 0 1 1-1h3.5a1 1 0 0 1 1 1c0 1.25.2 2.45.57 3.57a1 1 0 0 1-.25 1z"/></svg>
          <span>555.382.6519</span>
        </div>
      </address>
    </header>

    <section class="letter-body">
      <div class="letter-date">January-03-2020</div>
      <div class="recipient">Mr, Martin Alvey<br>President</div>
      <div class="recipient-company">Crestline Group<br>123 Street Name, Suite# 10<br>City, State, 120023</div>
      <div class="salutation">Dear Mr, Martin</div>
      <div class="letter-text">
        <p>Lorem ipsum dolor sit amet, consectetur adipiscing elit, sed do eiusmod tempor incididunt ut labore et dolore magna aliqua. Ut enim ad minim veniam, quis nostrud exercitation ullamco laboris nisi ut aliquip ex ea commodo consequat. Duis aute irure dolor in reprehenderit in voluptate velit esse cillum dolore eu fugiat nulla pariatur.</p>
        <p>Lorem ipsum dolor sit amet, consectetur adipiscing elit, sed do eiusmod tempor incididunt ut labore et dolore magna aliqua. Ut enim ad minim veniam, quis nostrud exercitation ullamco laboris nisi ut aliquip ex ea commodo consequat. Duis aute irure dolor in reprehenderit in voluptate velit esse cillum dolore eu fugiat nulla pariatur.</p>
        <p>Lorem ipsum dolor sit amet, consectetur adipiscing elit, sed do eiusmod tempor incididunt ut labore et dolore magna aliqua. Ut enim ad minim veniam, quis nostrud exercitation ullamco laboris nisi ut aliquip ex ea commodo consequat.</p>
        <p>Excepteur sint occaecat cupidatat non proident, sunt in culpa qui officia deserunt mollit anim id est laborum. re et dolore magnam aliquam quaerat voluptatem.</p>
      </div>
      <div class="closing">Regards</div>
      <div class="signature">Daniel Reyes</div>
    </section>
  </article>
</body>
</html>
```